Create Website for new company called "Verdale Lodge 37"

Verdale Lodge 37 is a new business situated in Southwestern Colorado. We are creating a business that will rent out spaces where clients can grow their own marijuana. Picture a large green house with partitioned spaces that are secured by a lock. Best way to envision this would be to think of a storage business that rents out storage rooms. The difference is that we will be having the units inside a green house ( for growing purposes) Picture a small area that is secured by locks, Picture an area that has the ability to provide state of the art security, cameras etc. We want to focus our efforts on professionals, blue collar workers and end users of marijuana. Our emphasis is in the area of assisting those whom wish to grow their own plants. We want to provide them a safe facility in which to do that. . Keep in mind that we also build custom grow rooms at clients homes and provide a grow pod (lease these) where a small grow unit will be delivered and picked up from our clients whom want to lease a unit for a short amount of time. We have a business card ( just designed) and will send that information to those whom express an interests in this project. We want to be able to sign people up for our services by entering an agreement and signing the agreement while on the internet. We want to provide our services to those whom consume recreational and medical marijuana. This site will need to gather information I.e email addresses so that we can followup with offers. This is a tremendous opportunity for the right designer. We will be creating many more websites as other states come on line and make marijuana legal to consume. Use the business card model for a point of reference of how we envision the concept. That is a business card we just recently printed. The hands and the plant is our logo so far. Open to suggestions. There will be three levels of service. Bronze, Silver, Gold or Platinum. We will also have a retail biz down the road but not at the present time.

Target Market(s)

Ages 21-60

Industry/Entity Type

Medical

Logo Text

Verdale Lodge 37.

Number of Pages Required

5+ page

Requirements
Must have
• Clean appearance not to busy , easily navigable from link to link, page to page. Must have ability down the road to enter into a contractual agreement via the website. Must use our provided logo and example of that is on our business card that will be uploaded here shortly. We would like to have the colors that are on the business card however if you have suggestions or color schemes that you want us to consider that is okay.
Nice to have
• Nice to have a animation of seed to weed and how clients can save a tremendous amount of money growing their own cannabis. Nice to have testimonial page or feedback page. Have a membership component to website,
Should not have
• No flashing lights, etc. Not to busy in terms of animations.

```html
<!DOCTYPE html>
<html lang="en">
<head>
<meta charset="utf-8">
<title>Verdale Lodge 37</title>
<link href="https://fonts.googleapis.com/css2?family=Open+Sans:wght@400;600;700&display=swap" rel="stylesheet">
<style>
:root{
  --green:#2f8a3b;
  --green-dark:#1d6e2f;
  --footer:#217a35;
  --footer-line:#3a9150;
  --orange:#e3711f;
  --text:#555;
  --head:#333;
  --light:#f2f2f2;
  --border:#e2e2e2;
}
*{box-sizing:border-box;margin:0;padding:0}
html,body{width:769px;height:1200px;overflow:hidden;background:#fff}
body{font-family:"Open Sans",Arial,sans-serif;color:var(--text);font-size:7px;line-height:1.45}
.site-header{height:80px;position:relative;padding:0 28px}
.brand{position:absolute;left:34px;top:14px;display:flex;align-items:center;gap:8px}
.brand-mark{width:22px;height:22px;border-radius:50%;background:var(--green)}
.brand-name{font-size:22px;font-weight:700;color:var(--green);letter-spacing:.5px}
.contacts{position:absolute;right:30px;top:26px;display:flex;gap:22px}
.contact strong{display:block;font-size:8px;color:var(--head);font-weight:700}
.contact span{display:block;font-size:6px;color:#777}
.main-nav{height:26px;border-top:1px solid var(--border);border-bottom:1px solid var(--border);display:flex;padding-left:30px}
.main-nav a{display:block;padding:0 18px;line-height:24px;font-size:7.5px;color:#444;text-decoration:none}
.main-nav a.active{background:var(--orange);color:#fff}
.hero{position:relative;height:420px;background:radial-gradient(ellipse at 70% 30%,#c9d9a4 0%,#8fae5c 30%,#4d7a2f 60%,#2c4d1c 100%)}
.hero-caption{position:absolute;left:96px;right:96px;top:296px;height:28px;background:rgba(20,40,15,.55);color:#fff;font-size:9px;line-height:28px;padding-left:16px}
.hero-arrow{position:absolute;top:190px;width:14px;height:24px;background:rgba(255,255,255,.55)}
.hero-arrow.left{left:0}.hero-arrow.right{right:0}
.hero-arrow svg{display:block;margin:6px auto}
h2.section-title{font-size:13px;font-weight:400;color:var(--head);margin-bottom:10px}
.about{position:absolute;left:38px;top:560px;width:440px}
.about-body{display:flex;gap:12px}
.about-photo{width:120px;height:76px;background:linear-gradient(#cfe0ef,#7f9ab5)}
.about-text{flex:1;font-size:6.2px}
.btn{display:inline-block;background:var(--orange);color:#fff;font-size:6.5px;padding:3px 10px;border-radius:2px;margin-top:6px}
.news{position:absolute;left:534px;top:560px;width:198px}
.news-panel{background:var(--light);padding:8px;height:242px}
.news-item{display:flex;gap:6px;margin-bottom:9px}
.news-thumb{width:30px;height:30px;background:linear-gradient(#7fae5b,#3c6b25)}
.news-item strong{display:block;font-size:7px;color:var(--head);font-weight:600}
.news-item p{font-size:5.5px}
.news-item em{font-style:normal;color:var(--orange);font-size:5px}
.news-panel .view-all{display:block;text-align:center;font-size:6px;margin-top:2px}
.gallery{position:absolute;left:38px;top:708px;width:480px}
.gallery-grid{display:flex;gap:14px}
.gallery-item{width:148px}
.gallery-img{height:90px}
.gallery-img.g1{background:linear-gradient(#9cc26f,#3e6d23)}
.gallery-img.g2{background:linear-gradient(#a9c38a,#56794a)}
.gallery-img.g3{background:linear-gradient(#5d7d3d,#c7b58a)}
.gallery-item p{text-align:center;font-size:7px;margin-top:4px}
.testimonials{position:absolute;left:38px;right:38px;top:912px}
.test-head{display:flex;justify-content:space-between;align-items:center}
.test-arrows{display:flex;gap:4px}
.test-arrows span{width:11px;height:11px;border-radius:50%;background:#ccc;display:block}
.test-arrows span.on{background:var(--orange)}
.test-grid{display:flex;gap:18px}
.test-card{flex:1}
.quote{border:1px solid var(--border);padding:10px;font-size:6px;height:56px;text-align:center}
.person{display:flex;align-items:center;gap:8px;margin-top:8px;padding-left:14px}
.avatar{width:22px;height:22px;border-radius:50%;background:#c8b3a0}
.person span{font-size:6.5px}
.dots{text-align:center;margin-top:8px}
.dots i{display:inline-block;width:5px;height:5px;border-radius:50%;background:#ccc;margin:0 2px}
.dots i.on{background:var(--green)}
.site-footer{position:absolute;left:0;right:0;top:1088px;bottom:0;background:var(--footer);color:#fff;padding:0 30px}
.footer-top{display:flex;align-items:center;height:34px;border-bottom:1px solid var(--footer-line)}
.footer-nav{display:flex;gap:24px;flex:1}
.footer-nav a{color:#fff;font-size:6.5px;text-decoration:none}
.footer-nav a.active{border:1px solid #fff;padding:2px 8px}
.social{display:flex;gap:4px}
.social span{width:10px;height:10px;background:rgba(255,255,255,.8);display:block;border-radius:2px}
.footer-info{display:flex;gap:30px;padding-top:12px;font-size:6px;align-items:center}
.footer-info .ico{display:inline-block;width:7px;height:7px;border-radius:50%;background:#fff;margin-right:4px;vertical-align:middle}
.footer-info .addr{width:150px}
.donate{margin-left:auto;background:var(--orange);padding:2px 9px;border-radius:8px;font-size:6px}
.copy{font-size:5.5px;margin-top:10px;opacity:.85}
</style>
</head>
<body>
<header class="site-header">
  <div class="brand"><span class="brand-mark"></span><span class="brand-name">Verdale Lodge 37</span></div>
  <div class="contacts">
    <div class="contact"><strong>Dorian Wexley</strong><span>cell 555.014.2261</span></div>
    <div class="contact"><strong>Elias Wexley</strong><span>elias@verdalelodge37.com</span></div>
    <div class="contact"><strong>Corwin Ashdale</strong><span>cell 555.017.3384</span></div>
  </div>
</header>
<nav class="main-nav">
  <a class="active">Home</a><a>About Us</a><a>Our Service</a><a>Our Blog</a><a>Gallery</a><a>Contact Us</a>
</nav>
<section class="hero" role="img" aria-label="Close-up photograph of green cannabis leaves in soft sunlight">
  <div class="hero-arrow left"><svg width="6" height="12"><path d="M5 1L1 6l4 5" stroke="#555" fill="none" stroke-width="1.5"/></svg></div>
  <div class="hero-arrow right"><svg width="6" height="12"><path d="M1 1l4 5-4 5" stroke="#555" fill="none" stroke-width="1.5"/></svg></div>
  <div class="hero-caption">We are creating a business that will rent out spaces where clients can grow their own marijuana</div>
</section>

<section class="about">
  <h2 class="section-title">About Us</h2>
  <div class="about-body">
    <div class="about-photo" role="img" aria-label="Photograph of a team of professionals"></div>
    <div class="about-text">
      <p>Verdale Lodge 37 offers secure, lockable grow spaces inside a large greenhouse in Southwestern Colorado. Each unit is monitored with modern cameras and controlled access, giving members a safe and private place to grow their own plants. We also build custom grow rooms at home and lease compact grow pods that we deliver and collect. Whether you are a professional, a working hand or a medical user, we help you grow with confidence and save money.</p>
      <span class="btn">Read More</span>
    </div>
  </div>
</section>

<aside class="news">
  <h2 class="section-title">Latest News</h2>
  <div class="news-panel">
    <div class="news-item"><div class="news-thumb" role="img" aria-label="Plant photo"></div><div><strong>Lorem ipsum</strong><p>New grow units open this spring for members.</p><em>Read more</em></div></div>
    <div class="news-item"><div class="news-thumb" role="img" aria-label="Plant photo"></div><div><strong>Company poplar</strong><p>Grow pods now available for short leases.</p><em>Read more</em></div></div>
    <div class="news-item"><div class="news-thumb" role="img" aria-label="Plant photo"></div><div><strong>Ipsum sit amet</strong><p>Tips for a healthy first harvest at home.</p><em>Read more</em></div></div>
    <div class="news-item"><div class="news-thumb" role="img" aria-label="Plant photo"></div><div><strong>Lorem ipsum</strong><p>Membership levels explained in simple terms.</p><em>Read more</em></div></div>
    <span class="view-all">View All</span>
  </div>
</aside>

<section class="gallery">
  <h2 class="section-title">Our Gallery</h2>
  <div class="gallery-grid">
    <div class="gallery-item"><div class="gallery-img g1" role="img" aria-label="Young cannabis plants"></div><p>Lorem ipsum dolor</p></div>
    <div class="gallery-item"><div class="gallery-img g2" role="img" aria-label="Greenhouse walkway"></div><p>Contentry pepi</p></div>
    <div class="gallery-item"><div class="gallery-img g3" role="img" aria-label="Harvested plant buds"></div><p>Sit dolor amet</p></div>
  </div>
</section>

<section class="testimonials">
  <div class="test-head"><h2 class="section-title">Client Testimonials</h2><div class="test-arrows"><span></span><span class="on"></span></div></div>
  <div class="test-grid">
    <div class="test-card"><p class="quote">A friend recommended this place and it has made growing my own so easy. The staff are kind and the units feel truly safe.</p><div class="person"><span class="avatar"></span><span>Nora Calloway</span></div></div>
    <div class="test-card"><p class="quote">Because I work long hours, the pod lease is perfect for me. It was a simple setup and I saved money in the first season.</p><div class="person"><span class="avatar"></span><span>Ivo Marsh</span></div></div>
    <div class="test-card"><p class="quote">It is a completely different experience from dealing with conventional dispensaries. Clean, secure and always friendly.</p><div class="person"><span class="avatar"></span><span>Lena Hart</span></div></div>
  </div>
  <div class="dots"><i class="on"></i><i></i><i></i></div>
</section>

<footer class="site-footer">
  <div class="footer-top">
    <div class="footer-nav"><a class="active">Home</a><a>About Us</a><a>Our Service</a><a>Our Blog</a><a>Gallery</a><a>Contact Us</a></div>
    <div class="social"><span></span><span></span><span></span><span></span></div>
  </div>
  <div class="footer-info">
    <div class="addr"><span class="ico"></span>47 Meadowbrook Lane, Pinecrest Valley</div>
    <div><span class="ico"></span>+1 555 014 2261</div>
    <div><span class="ico"></span>info@verdalelodge37.com</div>
    <span class="donate">Donate</span>
  </div>
  <p class="copy">Copyright 2015 Verdale Lodge 37. All rights reserved.</p>
</footer>
</body>
</html>
```